Velk Partners Building Business Cards

We need a business card that reflects our business as "Solar Experts" in San Diego. Browse our website www.velkpartners.example our License needs to be displayed as "CSLB# 3867140" our phone number is (619) 555-0187

Save thousands on your electric bills and increase the value of your home while helping to protect the environment. Our solar installation experts will help you design the system that's right for you, using only the highest quality equipment that will look great and give you ideal performance. Our goal is to make you energy independent, and get your electric bill to 0.

Paul Osterby
(619) 555-0187
paul@velkpartners.example

Target Market(s)

Home owners in san diego looking for solar

Industry/Entity Type

Solar Energy

Contact Information for Business Card

Paul Osterby
(619) 555-0187
paul@velkpartners.example

Font styles to use
Other font styles liked:
• Use our logo font

Requirements
Must have
• License needs to be displayed as "CSLB# 3867140" our phone number is (619) 555-0187
Nice to have
• Real images of rooftop home solar in san diego
Should not have
• our business address

```html
<!DOCTYPE html>
<html lang="en">
<head>
<meta charset="utf-8">
<title>Velk Partners Building – Business Cards</title>
<link href="https://fonts.googleapis.com/css2?family=Roboto:wght@400;500;700&display=swap" rel="stylesheet">
<style>
  :root {
    --stage: #aaa7a7;
    --navy: #2b4b93;
    --navy-deep: #203a78;
    --ink: #1f3a78;
    --gold: #f0a818;
    --white: #ffffff;
    --paper: #fbfbfa;
  }
  * { margin: 0; padding: 0; box-sizing: border-box; }
  html, body { width: 1200px; height: 1200px; overflow: hidden; }
  body {
    background: var(--stage);
    font-family: "Roboto", Arial, sans-serif;
    position: relative;
  }
  .card {
    position: absolute;
    width: 712px;
    height: 418px;
    border-radius: 28px;
    overflow: hidden;
  }
  /* ---------- Front ---------- */
  .card-front { left: 238px; top: 118px; }
  .front-backdrop {
    position: absolute; inset: 0;
    background: linear-gradient(160deg, #3556a0 0%, var(--navy) 55%, var(--navy-deep) 100%);
  }
  .front-logo {
    position: absolute; left: 0; right: 0; top: 50px;
    text-align: center; color: var(--white); font-weight: 700;
  }
  .front-logo .logo-main { display: block; font-size: 66px; line-height: 1; letter-spacing: -1px; }
  .front-logo .logo-sub { display: block; font-size: 30px; line-height: 1; margin-top: 12px; letter-spacing: 3px; text-transform: uppercase; }
  .process-title {
    position: absolute; left: 0; right: 0; top: 205px;
    display: flex; justify-content: center; align-items: center; gap: 26px;
    color: var(--white); font-size: 23px; font-weight: 500; letter-spacing: 4px;
  }
  .process-title .rule { width: 56px; height: 3px; background: var(--gold); }
  .process-steps { position: absolute; left: 0; top: 0; width: 712px; height: 418px; }
  .step-label {
    position: absolute; top: 336px; width: 160px; margin-left: -80px;
    text-align: center; color: var(--white); font-size: 14px; line-height: 15px;
  }
  /* ---------- Back ---------- */
  .card-back { left: 230px; top: 645px; background: var(--paper); }
  .holder-name { position: absolute; left: 32px; top: 40px; color: var(--ink); font-size: 25px; font-weight: 700; }
  .holder-role { position: absolute; left: 32px; top: 73px; color: var(--ink); font-size: 17px; }
  .contact-list { position: absolute; left: 32px; top: 273px; list-style: none; }
  .contact-list li { display: flex; align-items: center; height: 25px; color: var(--ink); font-size: 18px; }
  .contact-list svg { width: 20px; height: 16px; margin-right: 16px; }
  .contact-list .accent { color: var(--gold); }
  .license { position: absolute; left: 32px; top: 356px; color: var(--ink); font-size: 18px; }
  .back-logo {
    position: absolute; right: 30px; top: 312px; text-align: center;
    color: var(--ink); font-weight: 700;
  }
  .back-logo .logo-main { display: block; font-size: 40px; line-height: 1; letter-spacing: -0.5px; }
  .back-logo .logo-sub { display: block; font-size: 19px; line-height: 1; margin-top: 6px; letter-spacing: 2px; text-transform: uppercase; }
</style>
</head>
<body>

<section class="card card-front">
  <div class="front-backdrop" role="img" aria-label="Faint photo of rooftop solar panels under a blue overlay"></div>

  <div class="front-logo">
    <span class="logo-main">Velk Partners</span>
    <span class="logo-sub">Building Inc</span>
  </div>

  <div class="process-title"><span class="rule"></span>OUR PROCESS<span class="rule"></span></div>

  <svg class="process-steps" viewBox="0 0 712 418" aria-hidden="true">
    <g stroke="#ffffff" stroke-width="2.5" stroke-dasharray="2 3">
      <line x1="170" y1="290" x2="242" y2="290"/>
      <line x1="320" y1="290" x2="392" y2="290"/>
      <line x1="470" y1="290" x2="543" y2="290"/>
    </g>
    <g fill="#f0a818">
      <rect x="92" y="252" width="78" height="76"/>
      <rect x="242" y="252" width="78" height="76"/>
      <rect x="392" y="252" width="78" height="76"/>
      <rect x="543" y="252" width="78" height="76"/>
    </g>
    <!-- magnifier -->
    <g stroke="#1f3a78" fill="none" stroke-width="3.5" stroke-linecap="round">
      <circle cx="127" cy="286" r="11"/>
      <line x1="135" y1="294" x2="147" y2="306" stroke-width="6"/>
    </g>
    <!-- pencil -->
    <g transform="rotate(45 281 290)" fill="#1f3a78">
      <rect x="273" y="266" width="16" height="38" rx="2"/>
      <polygon points="273,306 289,306 281,320"/>
    </g>
    <!-- card -->
    <g fill="#1f3a78">
      <rect x="416" y="276" width="36" height="24" rx="3" transform="rotate(-12 434 288)"/>
      <rect x="410" y="282" width="40" height="26" rx="3"/>
      <rect x="410" y="287" width="40" height="5" fill="#f0a818"/>
      <rect x="414" y="298" width="12" height="4" fill="#f0a818"/>
    </g>
    <!-- tools -->
    <g stroke="#1f3a78" stroke-width="5" stroke-linecap="round">
      <line x1="566" y1="310" x2="598" y2="272"/>
      <line x1="566" y1="272" x2="598" y2="310"/>
    </g>
    <circle cx="600" cy="270" r="7" fill="none" stroke="#1f3a78" stroke-width="4"/>
  </svg>

  <div class="step-label" style="left:131px">Site<br>Evaluation</div>
  <div class="step-label" style="left:281px">Design &amp;<br>Permitting</div>
  <div class="step-label" style="left:431px">Purchase of<br>Materials</div>
  <div class="step-label" style="left:582px">Installation &amp;<br>Commissioning</div>
</section>

<section class="card card-back">
  <h1 class="holder-name">Paul Osterby</h1>
  <p class="holder-role">Managing Director</p>

  <ul class="contact-list">
    <li>
      <svg viewBox="0 0 20 16"><path fill="#f0a818" d="M2 5c0-3 16-3 16 0v2h-4V5H6v2H2z M5 8h10l2 7H3z"/></svg>
      (619) 555-0187
    </li>
    <li>
      <svg viewBox="0 0 20 16"><g fill="none" stroke="#f0a818" stroke-width="1.6"><circle cx="10" cy="8" r="7"/><ellipse cx="10" cy="8" rx="3" ry="7"/><line x1="3" y1="8" x2="17" y2="8"/></g></svg>
      paul@velkpartners.example
    </li>
    <li>
      <svg viewBox="0 0 20 16"><rect x="1" y="2" width="18" height="12" fill="#f0a818"/><polyline points="1,2 10,9 19,2" fill="none" stroke="#fbfbfa" stroke-width="1.6"/></svg>
      www.<span class="accent">velkpartners</span>.example
    </li>
  </ul>
  <p class="license">License: CSLB# 3867140</p>

  <div class="back-logo">
    <span class="logo-main">Velk Partners</span>
    <span class="logo-sub">Building Inc</span>
  </div>
</section>

</body>
</html>
```